Business Card Design

Hello,
I try and keep my business card fresh and current. So about every year i get a new one. This year I'd like something with a white background and black lettering.
Before you start - I do not want my phone number or any other description on the card other than my url and my email.

I'd like a double sided business card with
TomFarrow.com on one side

and

Tom@TomFarrow.com on the other side of the card

Thinking very minimalistic and modern.
I don't have a particular font i mind or how to capitalize my name or website. This card will lead people to my new website that is being designed to showcase my photography and music.

* Initial thought was the front side of the card having a grid-like pattern built out of dashes or periods, with my website sitting within the pattern and on the back side my email on a stark white background. But that might look completely lame - haha.

I'm looking forward to seeing what you come up with.

thank you,
- tom farrow
Updates

Project Deadline Extended
Reason: Want to spend some more time with the designs and add a little $. thanks for all the designs - tom

Project Deadline Extended

Wanted to add a little $ and spend some more time with the designs.

big thanks to all who have submitted work 

- tom

Industry/Entity Type

Business

Contact Information for Business Card

www.tomfarrow.com
tom@tomfarrow.com

Colors
000000
ffffff

Requirements
Must have
• tomfarrow.com
tom@tomfarrow.com
Should not have
• phone number
any description of what i do, photography or music

```html
<!DOCTYPE html>
<html lang="en">
<head>
<meta charset="utf-8">
<title>TomFarrow.com – Business Card</title>
<link href="https://fonts.googleapis.com/css2?family=Gabriela&display=swap" rel="stylesheet">
<style>
  :root {
    --backdrop: #3d4b4d;
    --ink: #000000;
    --paper: #ffffff;
    --panel-top: #ffffff;
    --panel-bottom: #f1f1f1;
    --panel-edge: rgba(0, 0, 0, 0.28);
  }
  html, body {
    margin: 0;
    padding: 0;
    width: 830px;
    height: 1200px;
    overflow: hidden;
    background: var(--backdrop);
  }
  .canvas {
    position: relative;
    width: 830px;
    height: 1200px;
  }
  .card {
    position: absolute;
    left: 36px;
    width: 765px;
    height: 451px;
    overflow: hidden;
    background: var(--paper);
    box-shadow: 0 10px 24px rgba(0, 0, 0, 0.35);
  }
  .card--front { top: 23px; }
  .card--back { top: 651px; }
  .card__shapes {
    position: absolute;
    inset: 0;
    width: 765px;
    height: 451px;
  }
  .card__text {
    position: absolute;
    margin: 0;
    font-family: "Gabriela", Georgia, serif;
    font-weight: 400;
    color: var(--ink);
    white-space: nowrap;
    line-height: 1;
  }
  .front__tab-url {
    top: 24px;
    right: 16px;
    font-size: 35px;
  }
  .front__url {
    top: 336px;
    left: 28px;
    font-size: 44px;
  }
  .back__email {
    top: 152px;
    left: 0;
    width: 765px;
    text-align: center;
    font-size: 56px;
  }
</style>
</head>
<body>
<main class="canvas">

  <section class="card card--front" aria-label="Front of business card">
    <svg class="card__shapes" viewBox="0 0 765 451" aria-hidden="true">
      <defs>
        <linearGradient id="panelFront" x1="0" y1="0" x2="0" y2="1">
          <stop offset="0" stop-color="var(--panel-top)"/>
          <stop offset="1" stop-color="var(--panel-bottom)"/>
        </linearGradient>
      </defs>
      <path class="front__tab" d="M392 0 C430 0 432 96 500 96 H765 V0 Z"
            fill="url(#panelFront)" stroke="var(--panel-edge)" stroke-width="1.5"/>
      <path class="front__panel" d="M0 268 H625 C700 268 742 300 765 451 H0 Z"
            fill="url(#panelFront)" stroke="var(--panel-edge)" stroke-width="1.5"/>
    </svg>
    <p class="card__text front__tab-url">TomFarrow.com</p>
    <p class="card__text front__url">TomFarrow.com</p>
  </section>

  <section class="card card--back" aria-label="Back of business card">
    <svg class="card__shapes" viewBox="0 0 765 451" aria-hidden="true">
      <defs>
        <linearGradient id="panelBack" x1="0" y1="0" x2="0" y2="1">
          <stop offset="0" stop-color="var(--panel-top)"/>
          <stop offset="1" stop-color="var(--panel-bottom)"/>
        </linearGradient>
      </defs>
      <rect class="back__band" x="0" y="0" width="765" height="96"
            fill="url(#panelBack)" stroke="var(--panel-edge)" stroke-width="1.5"/>
      <rect class="back__panel" x="0" y="272" width="765" height="179"
            fill="url(#panelBack)" stroke="var(--panel-edge)" stroke-width="1.5"/>
    </svg>
    <p class="card__text back__email">Tom@TomFarrow.com</p>
  </section>

</main>
</body>
</html>
```